SaaS Early tech startup business card design

Unique design for experience ecommerce platform company. the business cards will be used by executive members. conformance with color code is required.

```html
<!DOCTYPE html>
<html lang="en">
<head>
<meta charset="utf-8">
<title>Nuvel Business Card</title>
<link href="https://fonts.googleapis.com/css2?family=Arimo:wght@400;700&display=swap" rel="stylesheet">
<style>
  :root {
    --bg: #1b1b20;
    --card: #21213d;
    --card-edge: #2a2a4a;
    --teal: #17bfa0;
    --teal-deep: #1a86a8;
    --ink: #ffffff;
    --rule: #d9dbe6;
  }
  * { box-sizing: border-box; margin: 0; padding: 0; }
  html, body { width: 1200px; height: 900px; overflow: hidden; }
  body {
    background: var(--bg);
    font-family: "Arimo", Arial, sans-serif;
    position: relative;
  }
  .card {
    position: absolute;
    width: 680px;
    height: 390px;
    background: var(--card);
    border-radius: 26px;
    border: 1px solid var(--card-edge);
    overflow: hidden;
  }
  .card-front { left: 80px; top: 50px; }
  .card-back { left: 440px; top: 460px; }

  .brand {
    display: flex;
    align-items: center;
    gap: 18px;
  }
  .brand-name {
    font-weight: 700;
    color: var(--teal);
    letter-spacing: -2px;
    line-height: 1;
  }
  .brand-dot {
    border-radius: 50%;
    background: var(--teal-deep);
  }
  .card-front .brand {
    position: absolute;
    left: 150px;
    top: 128px;
  }
  .card-front .brand-name { font-size: 120px; }
  .card-front .brand-dot { width: 90px; height: 90px; }

  .card-back .brand {
    position: absolute;
    left: 0; right: 0;
    top: 46px;
    justify-content: center;
  }
  .card-back .brand-name { font-size: 100px; }

  .details {
    position: absolute;
    left: 0; right: 0;
    top: 185px;
    display: flex;
    justify-content: center;
    align-items: center;
  }
  .person {
    text-align: right;
    padding-right: 24px;
  }
  .person-name {
    font-weight: 700;
    font-size: 30px;
    color: var(--teal);
  }
  .person-role {
    font-size: 20px;
    color: var(--ink);
    margin-top: 2px;
  }
  .divider {
    width: 2px;
    height: 80px;
    background: var(--rule);
  }
  .contacts {
    list-style: none;
    padding-left: 24px;
  }
  .contacts li {
    display: flex;
    align-items: center;
    gap: 10px;
    font-size: 20px;
    color: var(--ink);
    line-height: 1.35;
  }
  .contact-icon {
    width: 22px; height: 22px;
    flex: none;
  }
  .address {
    position: absolute;
    left: 0; right: 0;
    bottom: 52px;
    text-align: center;
    font-size: 22px;
    color: var(--ink);
  }
</style>
</head>
<body>

<section class="card card-front" aria-label="Card front">
  <div class="brand">
    <span class="brand-name">nuvel</span>
    <span class="brand-dot"></span>
  </div>
</section>

<section class="card card-back" aria-label="Card back">
  <div class="brand">
    <span class="brand-name">nuvel</span>
  </div>

  <div class="details">
    <div class="person">
      <p class="person-name">Marcus Ellery</p>
      <p class="person-role">Manager</p>
    </div>
    <div class="divider"></div>
    <ul class="contacts">
      <li>
        <svg class="contact-icon" viewBox="0 0 22 22" aria-hidden="true">
          <rect width="22" height="22" rx="6" fill="var(--teal)"/>
          <path d="M7 5.5c1 0 1.6 2.3 1.6 2.8s-1 1-.8 1.6c.5 1.4 2.2 3.1 3.4 3.6.6.2 1-.8 1.6-.8s2.8.6 2.8 1.6c0 1-1.2 2-2.2 2C9 16.3 5.7 13 5.7 8 5.7 6.7 6.3 5.5 7 5.5z" fill="var(--card)"/>
        </svg>
        555-014-2290
      </li>
      <li>
        <svg class="contact-icon" viewBox="0 0 22 22" aria-hidden="true">
          <rect width="22" height="22" rx="6" fill="var(--teal)"/>
          <rect x="5" y="7" width="12" height="8.5" rx="1" fill="none" stroke="var(--card)" stroke-width="1.6"/>
          <path d="M5.5 7.5 11 12l5.5-4.5" fill="none" stroke="var(--card)" stroke-width="1.6"/>
        </svg>
        hello@nuvelmail.com
      </li>
      <li>
        <svg class="contact-icon" viewBox="0 0 22 22" aria-hidden="true">
          <rect width="22" height="22" rx="6" fill="var(--teal)"/>
          <circle cx="11" cy="11" r="6" fill="none" stroke="var(--card)" stroke-width="1.5"/>
          <ellipse cx="11" cy="11" rx="2.6" ry="6" fill="none" stroke="var(--card)" stroke-width="1.3"/>
          <path d="M5 11h12" stroke="var(--card)" stroke-width="1.3"/>
        </svg>
        www.nuvelcommerce.com
      </li>
    </ul>
  </div>

  <p class="address">Your address, city, state, ZIP 0000</p>
</section>

</body>
</html>
```